Create website for home automation - Control your lighting, fans, blinds etc remotely by smartphone

Plan for SHOPIFY Website - Our Clever Dwelling
Company name: Our Clever Dwelling
Company Slogan: Calm Evenings Come Naturally
Clean, Modern, Easy to Navigate, easy to maintain - not a lot of coding. We need flash technology but displaying simply what we do.
What we provide:
We will be offering wireless switch which can be added to iOS/Android App via WiFi, allowing users to remotely turn on/off connected lights, fans, security cameras, appliances, irrigation, humidifier separately from anywhere at any time.
Control your home away from home. No more wandering of your mind on those lights or appliances which you might have left switched on. No need to drive back home to check and switch them off. Save that energy, money and time just with a click of your phone no matter how far you are from home.
Replace your home electrical switches with smart switches. They retrofit existing electrical switches and allow you to make the transformation as needed.
Easy to use and intuitive app allows you to control your lights and devices just at a click. Set any kind of ambiance suiting your occasion.
Set scenes in smartphone app to group and operate your devices just at a button click. Same device can be included in more than one scene.
Collections and Products
Light Switches
Wall Plugs
Fan Switch
Pendants etc special lighting types.
Light Dimmers
Blind Controllers
Home Page:
Home page needs to telling customers what we do and how we do it in a few words to grab people.
Phone
Email
Support – Download instructions per product
Client login
Wholesale login
Promotional video to be on home screen - this is a short 1.5 - 2 min illustration introduction video to who we are and what we do - this is yet to be created)
Social media link - Facebook
Pages:
FAQ
About Us
Support/Shipping/Returns policy
Support/Installation
Blog posts
Product pages:
Description
Price
Space for where a video will be featured - how each product works/installation.
Reviews
Our competition:
http://www.brivo.com.au
https://lumigardenhub.com.au/2018/04/05/best-smart-light-switches-and-plugs/
https://www.tavelinq.com

```html
<!DOCTYPE html>
<html lang="en">
<head>
<meta charset="utf-8">
<title>Our Clever Dwelling</title>
<link href="https://fonts.googleapis.com/css2?family=Montserrat:wght@400;500;600;700;800&family=Open+Sans:wght@400;600;700&display=swap" rel="stylesheet">
<style>
:root{
  --navy:#101d6b;
  --navy-deep:#0c1656;
  --blue:#1d5fb8;
  --ink:#1b1b1b;
  --body:#3a3a3a;
  --topbar:#efeeec;
  --card:#f7f5f4;
  --section-grey:#f3f2f1;
  --white:#fff;
  --sale:#1d5fb8;
}
*{box-sizing:border-box;margin:0;padding:0}
html,body{width:1200px;height:3830px;overflow:hidden;background:var(--white)}
body{position:relative;font-family:"Open Sans",Arial,sans-serif;color:var(--body)}
.abs{position:absolute}
.heading{font-family:"Montserrat",Arial,sans-serif;font-weight:800;color:var(--ink);text-transform:uppercase;text-align:center}

/* top bar */
.topbar{left:0;top:0;width:1200px;height:36px;background:var(--topbar);font-size:13px;color:#333}
.topbar .ship{position:absolute;left:0;width:1200px;top:9px;text-align:center}
.topbar .links{position:absolute;right:30px;top:10px;display:flex;gap:22px;font-size:12px;align-items:center}
.topbar .links svg{vertical-align:-2px;margin-right:4px}

/* header */
.search{left:145px;top:102px;width:250px;height:32px;border:1px solid #ddd;font-size:11px;color:#999;padding:8px 10px}
.search svg{position:absolute;right:10px;top:9px}
.brand{left:0;width:1200px;top:60px;text-align:center}
.brand .mark{display:inline-block;width:64px;height:64px;border-radius:50%;background:var(--navy)}
.brand .name{font-family:"Montserrat",Arial,sans-serif;font-weight:800;font-size:23px;line-height:26px;color:var(--navy);letter-spacing:.5px;margin-top:10px}
.brand .tag{font-family:"Montserrat",Arial,sans-serif;font-weight:800;font-size:9px;color:var(--navy);letter-spacing:2px}
.nav{left:0;width:1200px;top:196px;display:flex;justify-content:center;gap:36px;font-family:"Montserrat",Arial,sans-serif;font-size:12px;font-weight:600;color:#222}
.nav .active{color:var(--blue);border-bottom:2px solid var(--blue);padding-bottom:4px}

/* hero */
.hero{left:0;top:232px;width:1200px;height:588px;overflow:hidden;
  background:
    radial-gradient(ellipse 190px 300px at 690px 210px,rgba(30,30,34,.85),rgba(30,30,34,0) 70%),
    radial-gradient(ellipse 160px 220px at 720px 470px,rgba(210,160,130,.75),rgba(210,160,130,0) 70%),
    radial-gradient(ellipse 320px 260px at 1060px 180px,rgba(255,255,255,.8),rgba(255,255,255,0) 70%),
    radial-gradient(ellipse 420px 200px at 250px 520px,rgba(235,232,226,.7),rgba(235,232,226,0) 70%),
    linear-gradient(90deg,#6f5f52 0%,#9e8c7c 22%,#c9beb2 45%,#ddd8d2 70%,#c2b8ae 100%)}
.hero::before{content:"";position:absolute;inset:0;background:linear-gradient(90deg,rgba(20,15,10,.35) 0%,rgba(20,15,10,0) 55%)}
.hero h1{position:absolute;left:145px;top:272px;font-family:"Montserrat",Arial,sans-serif;font-weight:800;font-size:44px;line-height:50px;color:var(--white);text-transform:uppercase;text-shadow:0 2px 8px rgba(0,0,0,.25)}
.hero .cta{position:absolute;left:145px;top:396px;width:393px;height:46px;background:var(--blue);color:var(--white);font-family:"Montserrat",Arial,sans-serif;font-weight:700;font-size:15px;text-align:center;line-height:46px;text-transform:uppercase}
.dots{position:absolute;left:0;width:1200px;top:530px;display:flex;justify-content:center;gap:16px;align-items:center}
.dots span{width:9px;height:9px;border-radius:50%;background:var(--white)}
.dots .on{width:13px;height:13px;background:var(--white);border:3px solid var(--blue)}

/* features */
.feature{top:845px;width:296px;height:230px;background:var(--navy);color:var(--white);text-align:center}
.feature svg{margin-top:40px}
.feature h3{font-family:"Montserrat",Arial,sans-serif;font-weight:700;font-size:15px;text-transform:uppercase;margin-top:24px}
.feature p{font-size:12px;margin-top:4px;opacity:.9}

/* products */
.rule{height:3px;background:#999;width:50px}
.product{top:1215px;width:222px;height:325px;background:var(--card);border:1px solid #ece9e6;text-align:center}
.product .shot{margin:36px auto 0;width:118px;height:180px;border-radius:8px;box-shadow:2px 6px 10px rgba(0,0,0,.18)}
.product .wide{width:150px;height:150px;margin-top:50px}
.product h4{font-family:"Montserrat",Arial,sans-serif;font-weight:500;font-size:13px;color:#222;margin-top:36px}
.product .price{font-size:13px;margin-top:8px}
.product .price s{color:#777;margin-right:6px}
.product .price b{color:var(--sale);font-weight:400}

/* what we do */
.whatwedo{left:0;top:1606px;width:1200px;height:511px;overflow:hidden;
  background:
    radial-gradient(ellipse 230px 150px at 600px 430px,rgba(150,150,150,.55),rgba(150,150,150,0) 75%),
    radial-gradient(ellipse 420px 180px at 600px 120px,rgba(120,80,55,.55),rgba(120,80,55,0) 75%),
    radial-gradient(ellipse 260px 200px at 120px 300px,rgba(70,85,60,.7),rgba(70,85,60,0) 75%),
    radial-gradient(ellipse 260px 200px at 1080px 300px,rgba(70,85,60,.7),rgba(70,85,60,0) 75%),
    linear-gradient(180deg,#2f2a26 0%,#5a4a3c 45%,#2a2624 100%)}
.whatwedo::before{content:"";position:absolute;inset:0;background:rgba(10,10,10,.35)}
.whatwedo h2{position:absolute;left:0;width:1200px;top:86px;font-size:36px;color:var(--white)}
.whatwedo p{position:absolute;left:378px;width:444px;top:146px;text-align:center;color:#eee;font-size:13.5px;line-height:21px}

/* how we do */
.how-title{left:143px;top:2257px;font-size:25px;text-align:left}
.how-text{left:143px;top:2315px;width:315px;font-size:13.5px;line-height:20px;color:#333}
.btn{background:var(--blue);color:var(--white);font-family:"Montserrat",Arial,sans-serif;font-weight:700;font-size:11px;text-transform:uppercase;text-align:center}
.how-btn{left:143px;top:2502px;width:118px;height:40px;line-height:40px}
.how-media{left:528px;top:2186px;width:529px;height:424px;overflow:hidden;box-shadow:0 2px 6px rgba(0,0,0,.15);
  background:
    radial-gradient(ellipse 70px 60px at 310px 70px,rgba(255,230,160,.95),rgba(255,230,160,0) 75%),
    radial-gradient(ellipse 80px 140px at 240px 240px,rgba(70,120,200,.85),rgba(70,120,200,0) 75%),
    radial-gradient(ellipse 200px 90px at 380px 330px,rgba(240,235,225,.8),rgba(240,235,225,0) 75%),
    radial-gradient(ellipse 160px 120px at 420px 140px,rgba(170,150,120,.8),rgba(170,150,120,0) 75%),
    linear-gradient(135deg,#6a4f38 0%,#b89468 40%,#a07d58 70%,#5c4430 100%)}
.play{position:absolute;left:242px;top:190px}

/* blog */
.blog{left:0;top:2701px;width:1200px;height:697px;background:var(--section-grey)}
.blog-shot{top:2857px;height:324px}
.blog-title{top:3214px;width:429px;text-align:center;font-family:"Montserrat",Arial,sans-serif;font-weight:600;font-size:14px;color:#222}
.blog-text{top:3244px;width:429px;padding:0 50px;text-align:center;font-size:12px;line-height:16px;color:#444}
.blog-btn{top:3319px;width:96px;height:28px;line-height:28px;font-size:10px}

/* footer */
.footer{left:0;top:3398px;width:1200px;height:432px;background:var(--navy);color:var(--white)}
.footer h5{font-family:"Montserrat",Arial,sans-serif;font-weight:700;font-size:13px;text-transform:uppercase;position:absolute}
.footer p,.footer li{font-size:12px;line-height:16px}
.footer ul{list-style:none;position:absolute}
.footer ul li{line-height:19px}
.subscribe{position:absolute;left:740px;top:128px;width:318px;height:38px;background:var(--white);color:#666;font-size:12px;padding:11px 12px}
.subscribe svg{position:absolute;right:10px;top:12px}
.social{position:absolute;left:742px;top:208px;display:flex;gap:26px}
.social span{width:18px;height:18px;border-radius:50%;border:2px solid var(--white)}
.divider{position:absolute;left:143px;top:290px;width:914px;height:1px;background:rgba(255,255,255,.18)}
.cards{position:absolute;left:0;width:1200px;top:340px;display:flex;justify-content:center;gap:6px}
.cards span{width:38px;height:24px;background:var(--white);border-radius:3px}
.copy{position:absolute;left:0;width:1200px;top:384px;text-align:center;font-size:11px;color:#cfd4ea}
</style>
</head>
<body>

<div class="abs topbar">
  <div class="ship">Free Shipping on all orders</div>
  <div class="links"><span>Wholesale login</span><span>Client login</span><span>Account</span>
    <span><svg width="14" height="12" viewBox="0 0 14 12"><path d="M0 1h2.5l2 7h7l1.5-5H4" fill="none" stroke="#333" stroke-width="1.4"/><circle cx="5.5" cy="10.5" r="1.2" fill="#333"/><circle cx="10.5" cy="10.5" r="1.2" fill="#333"/></svg>Cart (0)</span></div>
</div>

<div class="abs search">Search
  <svg width="12" height="12" viewBox="0 0 12 12"><circle cx="5" cy="5" r="3.8" fill="none" stroke="#222" stroke-width="1.6"/><path d="M8 8l3 3" stroke="#222" stroke-width="1.8"/></svg>
</div>

<div class="abs brand">
  <span class="mark"></span>
  <div class="name">OUR CLEVER DWELLING</div>
  <div class="tag">CALM EVENINGS COME NATURALLY</div>
</div>

<nav class="abs nav">
  <span class="active">HOME</span><span>ABOUT US</span><span>BLOG</span><span>PRODUCTS</span><span>FAQ</span><span>SUPPORT</span>
</nav>

<section class="abs hero" role="img" aria-label="Hand holding a smartphone showing a home control app in a bright living room">
  <h1>Calm Evenings<br>Come Naturally</h1>
  <div class="cta">Download instructions per product</div>
  <div class="dots"><span></span><span></span><span class="on"></span><span></span><span></span></div>
</section>

<div class="abs feature" style="left:143px">
  <svg width="70" height="70" viewBox="0 0 70 70" fill="none" stroke="#fff" stroke-width="2.5"><path d="M35 8a27 27 0 1 1-24 15"/><path d="M6 20l5 3 3-6"/><path d="M20 36l15-13 15 13M25 32v16h20V32"/><rect x="31" y="38" width="8" height="10"/></svg>
  <h3>Easy Installation</h3><p>Lorem Ipsum is simply dummy</p>
</div>
<div class="abs feature" style="left:452px">
  <svg width="70" height="70" viewBox="0 0 70 70" fill="none" stroke="#fff" stroke-width="2.5"><rect x="20" y="6" width="28" height="56" rx="4"/><path d="M30 56h8"/><rect x="28" y="30" width="16" height="12" rx="1"/><path d="M31 30v-5a5 5 0 0 1 10 0v5"/></svg>
  <h3>Security &amp; Safety</h3><p>Lorem Ipsum is simply dummy</p>
</div>
<div class="abs feature" style="left:761px">
  <svg width="70" height="70" viewBox="0 0 70 70" fill="none" stroke="#fff" stroke-width="2.5"><rect x="16" y="6" width="26" height="44" rx="3"/><path d="M36 62V36a4 4 0 0 1 8 0v8l8 2a5 5 0 0 1 4 6l-2 10"/></svg>
  <h3>Smart Technology</h3><p>Lorem Ipsum is simply dummy</p>
</div>

<h2 class="abs heading" style="left:0;width:1200px;top:1132px;font-size:25px">Our Products</h2>
<div class="abs rule" style="left:575px;top:1172px"></div>

<div class="abs product" style="left:143px"><div class="shot" role="img" aria-label="White wall power outlet" style="background:linear-gradient(155deg,#fbfbf8 0%,#e6e4de 55%,#c4c2bb 100%)"></div><h4>Wall Plug</h4><div class="price"><s>$25.00</s><b>$15.00</b></div></div>
<div class="abs product" style="left:373px"><div class="shot wide" role="img" aria-label="White light dimmer switch plate" style="background:linear-gradient(155deg,#fdfdfc 0%,#e8e8e5 55%,#c2c2be 100%)"></div><h4 style="margin-top:66px">Light Dimmer</h4><div class="price"><s>$25.00</s><b>$15.00</b></div></div>
<div class="abs product" style="left:603px"><div class="shot" role="img" aria-label="White toggle light switch" style="width:100px;background:linear-gradient(155deg,#fbfbfa 0%,#e7e7e4 55%,#c6c6c2 100%)"></div><h4>Light Switche</h4><div class="price"><s>$25.00</s><b>$15.00</b></div></div>
<div class="abs product" style="left:835px"><div class="shot" role="img" aria-label="Black round fan speed dial" style="border-radius:50%;width:160px;height:160px;margin-top:44px;background:radial-gradient(circle at 45% 40%,#3a3a3a,#111 60%,#050505)"></div><h4 style="margin-top:48px">Fan Switch</h4><div class="price"><s>$25.00</s><b>$15.00</b></div></div>

<section class="abs whatwedo" role="img" aria-label="Darkened photo of hands holding a home control tablet in front of a house">
  <h2 class="heading">What We Do</h2>
  <p>Contrary to popular belief, Lorem Ipsum is not simply random text. It has roots in a piece of classical Latin literature from 45 BC, making it over 2000 years old. Edwin Harlowe, a Latin professor at Larchmont Hill College in Vermont.</p>
</section>

<h2 class="abs heading how-title">How We Do</h2>
<p class="abs how-text">There are many variations of passages of Lorem Ipsum available, but the majority have suffered alteration in some form, by injected humour, or randomised words which don't look even slightly believable. If you are going to use a passage of Lorem Ipsum, you need to be sure there isn't anything embarrassing hidden in the middle of text.</p>
<div class="abs btn how-btn">Read More</div>
<div class="abs how-media" role="img" aria-label="Promotional video: hand holding a phone with a home app in a furnished living room">
  <svg class="play" width="46" height="46" viewBox="0 0 46 46"><circle cx="23" cy="23" r="22" fill="#fff"/><path d="M18 14l14 9-14 9z" fill="#1d5fb8"/></svg>
</div>

<section class="abs blog"></section>
<h2 class="abs heading" style="left:0;width:1200px;top:2758px;font-size:25px">Latest Blog</h2>
<div class="abs rule" style="left:575px;top:2798px"></div>

<div class="abs blog-shot" style="left:164px;width:428px;background:radial-gradient(ellipse 110px 110px at 280px 150px,rgba(230,240,255,.8),rgba(230,240,255,0) 75%),radial-gradient(ellipse 200px 170px at 280px 170px,rgba(60,110,170,.7),rgba(60,110,170,0) 75%),linear-gradient(135deg,#2b4565 0%,#6f8eae 45%,#9fb6cc 60%,#22384f 100%)" role="img" aria-label="Hand touching a glowing smart home interface"></div>
<div class="abs blog-shot" style="left:613px;width:429px;background:radial-gradient(ellipse 150px 100px at 260px 150px,rgba(40,60,80,.7),rgba(40,60,80,0) 75%),radial-gradient(ellipse 120px 90px at 150px 200px,rgba(215,180,160,.6),rgba(215,180,160,0) 75%),linear-gradient(135deg,#b7c5d1 0%,#6e8193 50%,#d2dae1 100%)" role="img" aria-label="Hands using a tablet on a desk"></div>

<div class="abs blog-title" style="left:164px">Contrary to popular belief orem Ipsu</div>
<p class="abs blog-text" style="left:164px">There are many variations of passages of Lorem Ipsum available, but the majority have suffered alteration in some form, by injected humour, or randomised</p>
<div class="abs btn blog-btn" style="left:330px">Read More</div>

<div class="abs blog-title" style="left:613px">Contrary to popular belief orem Ipsu</div>
<p class="abs blog-text" style="left:613px">There are many variations of passages of Lorem Ipsum available, but the majority have suffered alteration in some form, by injected humour, or randomised</p>
<div class="abs btn blog-btn" style="left:779px">Read More</div>

<footer class="abs footer">
  <h5 style="left:145px;top:64px">About Us</h5>
  <p style="position:absolute;left:145px;top:100px;width:262px">There are many variations of passages of Lorem Ipsum available, but the majority have suffered embarrassing hidden in the middle of text. All the Lorem Ipsum generators</p>
  <p style="position:absolute;left:145px;top:194px;font-weight:700;font-size:13px">
    <svg width="12" height="12" viewBox="0 0 12 12" style="vertical-align:-1px;margin-right:10px"><path d="M2 1l3 0 1 3-2 1a7 7 0 0 0 3 3l1-2 3 1v3a1 1 0 0 1-1 1A10 10 0 0 1 1 2a1 1 0 0 1 1-1z" fill="#fff"/></svg>555.014.2290</p>
  <p style="position:absolute;left:145px;top:222px;font-weight:700;font-size:13px">
    <svg width="12" height="10" viewBox="0 0 12 10" style="vertical-align:-1px;margin-right:10px"><rect width="12" height="10" fill="#fff"/><path d="M0 0l6 5 6-5" fill="none" stroke="#101d6b" stroke-width="1.3"/></svg>ourcleverdwelling.com</p>

  <h5 style="left:547px;top:64px">Menu</h5>
  <ul style="left:547px;top:100px"><li>Home</li><li>Products</li><li>FAQ</li><li>About Us</li><li>Support</li><li>Blog</li></ul>

  <h5 style="left:740px;top:64px">Connect</h5>
  <p style="position:absolute;left:740px;top:92px">Join our mailing list to get updates</p>
  <div class="subscribe">E-mail id
    <svg width="18" height="14" viewBox="0 0 18 14"><rect width="18" height="14" fill="#101d6b"/><path d="M1 1l8 7 8-7" fill="none" stroke="#fff" stroke-width="1.5"/></svg>
  </div>
  <div class="social"><span></span><span></span><span></span></div>

  <div class="divider"></div>
  <div class="cards"><span></span><span></span><span></span><span></span><span></span><span></span></div>
  <div class="copy">Copyrights @ 2018 All Rights Reserved</div>
</footer>

</body>
</html>
```